Real Estate Company Looking for Business Card Designs for 3 Executives

Hello!
Thanks so much for considering our project! We are a real estate investment company located in Edmonton, Alberta called Bellhaven Group of Companies. We invest/develop both commercial and residential real estate and are looking to create 3 DOUBLE-SIDED business cards for 3 top executives in the company! (for some reason it won't let us select the double-sided option, but yes, the cards are double sided and would be happy to tip extra)

We have certain guidelines that we want our business cards to for sure follow - the back of the Business card has to be the Black Background Version of the Logo which has already been designed and linked as a file (first file). We want the entire back of the card to simply just be the black background logo. In terms of the front of the card, would like to see a smaller version of the white background logo (linked as the second file) in the top left hand corner - of course, feel free to get creative and we can make revisions together along the way! and Then after that, just text. We want the card to be sharp, clean, easy on the eyes and highly professional looking. We would like the card to include the Full name of the Company (Bellhaven Group of Companies), Name of the Person, Title, Phone, Email. If possible please provide the front part of the card for 3 people:

1) Bellhaven Group of Companies, Liora Quenby, Chief Financial Officer, 780-555-0142, lioraquenby@bellhavengroup.example

2) Bellhaven Group of Companies, Tobias Quenby, Chief Executive Officer, 780-555-0187, tobiasquenby@bellhavengroup.example

3) Bellhaven Group of Companies, Rui Delcourt, Chief Operations Officer, 587-555-0163, ruidelcourt@bellhavengroup.example

Thank you so much for considering our project & we look forward to seeing your designs!

```html
<!DOCTYPE html>
<html lang="en">
<head>
<meta charset="utf-8">
<title>Bellhaven Group of Companies – Executive Business Cards</title>
<link rel="stylesheet" href="https://fonts.googleapis.com/css2?family=Arimo:wght@400;700&display=swap">
<style>
  :root {
    --stage: #1c1c1c;
    --card-black: #0b0709;
    --card-white: #ffffff;
    --ink-light: #f4f8f8;
    --ink-muted: #c9cdcd;
    --ink-dark: #0b0709;
  }
  * { box-sizing: border-box; margin: 0; padding: 0; }
  html, body {
    width: 1200px;
    height: 1015px;
    overflow: hidden;
    background: var(--stage);
    font-family: "Arimo", Arial, sans-serif;
  }
  .stage {
    width: 1200px;
    height: 1015px;
    display: grid;
    grid-template-columns: repeat(2, 560px);
    grid-template-rows: repeat(2, 320px);
    gap: 48px 40px;
    justify-content: center;
    align-content: center;
  }
  .card {
    width: 560px;
    height: 320px;
    position: relative;
    overflow: hidden;
    background: var(--card-black);
  }
  .brand {
    display: flex;
    align-items: center;
    gap: 12px;
  }
  .brand__mark {
    width: 12px;
    height: 12px;
    background: currentColor;
    flex: none;
  }
  .brand__name {
    font-weight: 400;
    letter-spacing: 0.4em;
    text-transform: uppercase;
    white-space: nowrap;
  }

  /* Back of card */
  .card--back {
    display: flex;
    flex-direction: column;
    align-items: center;
    justify-content: center;
    color: var(--ink-light);
  }
  .card--back .brand__name { font-size: 26px; }
  .card--back .brand__mark { width: 14px; height: 14px; }
  .website {
    margin-top: 42px;
    font-size: 14px;
    letter-spacing: 0.06em;
  }

  /* Front of card */
  .card--front { display: flex; }
  .front__logo-panel {
    width: 40%;
    flex: none;
    background: var(--card-white);
    color: var(--ink-dark);
    display: flex;
    align-items: center;
    justify-content: center;
  }
  .front__logo-panel .brand { gap: 10px; }
  .front__logo-panel .brand__name { font-size: 16px; letter-spacing: 0.28em; }
  .front__logo-panel .brand__mark { width: 9px; height: 9px; }
  .front__details {
    flex: 1;
    min-width: 0;
    color: var(--ink-light);
    padding: 58px 18px 0 30px;
  }
  .company {
    font-size: 10.5px;
    letter-spacing: 0.14em;
    text-transform: uppercase;
    color: var(--ink-muted);
    margin-bottom: 16px;
    white-space: nowrap;
  }
  .person__name {
    font-weight: 700;
    font-size: 19px;
    letter-spacing: 0.02em;
    text-transform: uppercase;
    white-space: nowrap;
  }
  .person__title {
    font-size: 14px;
    margin-top: 3px;
  }
  .contact {
    list-style: none;
    margin-top: 30px;
    font-size: 13px;
  }
  .contact li {
    display: flex;
    align-items: center;
    gap: 7px;
    margin-bottom: 5px;
    white-space: nowrap;
  }
  .contact svg { width: 12px; height: 12px; flex: none; }
</style>
</head>
<body>
  <main class="stage">
    <section class="card card--back" aria-label="Back of card">
      <div class="brand">
        <span class="brand__mark"></span>
        <span class="brand__name">Bellhaven</span>
      </div>
      <p class="website">www.bellhavengroup.example</p>
    </section>

    <section class="card card--front" aria-label="Front of card – Chief Financial Officer">
      <div class="front__logo-panel">
        <div class="brand"><span class="brand__mark"></span><span class="brand__name">Bellhaven</span></div>
      </div>
      <div class="front__details">
        <p class="company">Bellhaven Group of Companies</p>
        <h2 class="person__name">Liora Quenby</h2>
        <p class="person__title">Chief Financial Officer</p>
        <ul class="contact">
          <li><svg viewBox="0 0 24 24" aria-hidden="true"><path fill="none" stroke="#f4f8f8" stroke-width="2.2" stroke-linejoin="round" d="M6.6 3.5l3 3.6-1.9 2.3a12 12 0 0 0 6.9 6.9l2.3-1.9 3.6 3-2 2.6c-8.2-.5-14.9-7.2-15.4-15.4z"/></svg>780-555-0142</li>
          <li><svg viewBox="0 0 24 24" aria-hidden="true"><rect x="2" y="5" width="20" height="14" fill="#f4f8f8"/><path d="M2 5l10 8 10-8" fill="none" stroke="#0b0709" stroke-width="1.6"/></svg>lioraquenby@bellhavengroup.example</li>
        </ul>
      </div>
    </section>

    <section class="card card--front" aria-label="Front of card – Chief Executive Officer">
      <div class="front__logo-panel">
        <div class="brand"><span class="brand__mark"></span><span class="brand__name">Bellhaven</span></div>
      </div>
      <div class="front__details">
        <p class="company">Bellhaven Group of Companies</p>
        <h2 class="person__name">Tobias Quenby</h2>
        <p class="person__title">Chief Executive Officer</p>
        <ul class="contact">
          <li><svg viewBox="0 0 24 24" aria-hidden="true"><path fill="none" stroke="#f4f8f8" stroke-width="2.2" stroke-linejoin="round" d="M6.6 3.5l3 3.6-1.9 2.3a12 12 0 0 0 6.9 6.9l2.3-1.9 3.6 3-2 2.6c-8.2-.5-14.9-7.2-15.4-15.4z"/></svg>780-555-0187</li>
          <li><svg viewBox="0 0 24 24" aria-hidden="true"><rect x="2" y="5" width="20" height="14" fill="#f4f8f8"/><path d="M2 5l10 8 10-8" fill="none" stroke="#0b0709" stroke-width="1.6"/></svg>tobiasquenby@bellhavengroup.example</li>
        </ul>
      </div>
    </section>

    <section class="card card--front" aria-label="Front of card – Chief Operations Officer">
      <div class="front__logo-panel">
        <div class="brand"><span class="brand__mark"></span><span class="brand__name">Bellhaven</span></div>
      </div>
      <div class="front__details">
        <p class="company">Bellhaven Group of Companies</p>
        <h2 class="person__name">Rui Delcourt</h2>
        <p class="person__title">Chief Operations Officer</p>
        <ul class="contact">
          <li><svg viewBox="0 0 24 24" aria-hidden="true"><path fill="none" stroke="#f4f8f8" stroke-width="2.2" stroke-linejoin="round" d="M6.6 3.5l3 3.6-1.9 2.3a12 12 0 0 0 6.9 6.9l2.3-1.9 3.6 3-2 2.6c-8.2-.5-14.9-7.2-15.4-15.4z"/></svg>587-555-0163</li>
          <li><svg viewBox="0 0 24 24" aria-hidden="true"><rect x="2" y="5" width="20" height="14" fill="#f4f8f8"/><path d="M2 5l10 8 10-8" fill="none" stroke="#0b0709" stroke-width="1.6"/></svg>ruidelcourt@bellhavengroup.example</li>
        </ul>
      </div>
    </section>
  </main>
</body>
</html>
```